Stationery Design Project

We need a stationery design for our Norwegian trucking company. We have existed for about 15 years and our 12 drivers uses relatively new vehicles to transport goods around in northern Norway. Long distance routes with fresh fish og food transport is our main operations.

We have already made alogo that's printed on our trucks. The logo and a picture of our trucks is attached. I think the logo i crappy, but since its already in use, changing it is not an option in this round. Still using a better colour scheme in the overall stationery and more interesting fonts is possible (altso in the logo).

Company details:
Name: Kjelvraket AS
Organisation nr 873 615 309
Post adress: 8642 Raudvik

I like minimalism and simplicity. I am avalibly for questions in normal GMT working hours either here or on mail: ivar@fjordlast.no

Reason: Hi. Im extending the deadline because I needed some time to find a vector file of our logo. Sorry for the inconvenience

Hi, and thanks for all your interest in the project. Some updates:

-          I have decided to commit to using one of the designs. Some designer will get the payment.

-          I have extended the deadline with 24 hours since I needed some time to find our firms vector logo (a slow Swedish man was holding me up)

-          We will not choose a design before the deadline. No need to rush.

-          We have received a lot of great design and think there is a need to specified the product we want to make:

o   Business Card for all our employers. I just need the design and will duplicate with the correct numbers and name myself. The information on should be: Logo, employer’s name, Phone number, email, website, Postal number and address. Use this as a template: logo, Leif Brattvoll, 47382066, Leif@fjordlast.no,, fjordlast.no, 8642 Raudvik. The order and placement of the information is your creative decision.

o   Stickers to put on the goods we travel. On the sticker the should be the following information: Logo, phone number, Tekst and link: Fraktæ av Kjelvraket. Ke du syns? Fjordlast.no/tilbakemelding (this means: Handled by Kjelvraket. What do you think Fjordlast.no/feedback -à the link will be a feedback form). The placement the information and size is your creative decision with some stings: we have been thinking of using Drukko for printing and see that a size about 6x6 cm, 8x5 or something like that. (with 3000 copies our budget is 200 punds). Any suggestions of other suppliers are welcome. Drukko price calculator http://www.drukkolabelhouse.co.uk/digital-litho-printing/printing-labels-tags/stickers/

o   Letterhead with logo, address, phone number and organizational number.

o   Envelopes with logo,address, phone number and organizational number.

Have a nice day.

 

 

• Using the blue colour in the logo and using a similar graphic approch.

```html
<!DOCTYPE html>
<html lang="no">
<head>
<meta charset="utf-8">
<title>Kjelvraket – Visittkort</title>
<link href="https://fonts.googleapis.com/css2?family=Saira:wght@400;600&display=swap" rel="stylesheet">
<style>
  :root {
    --backdrop: #e6e8eb;
    --paper: #ffffff;
    --ink: #1f1f1f;
    --ink-soft: #3a3a3a;
    --brand-deep: #0b3a8e;
    --brand-mid: #1672d2;
    --brand-light: #3d92e4;
    --rule: #2f56a6;
  }
  * { box-sizing: border-box; margin: 0; padding: 0; }
  html, body {
    width: 1200px;
    height: 960px;
    overflow: hidden;
    background: var(--backdrop);
    font-family: "Saira", Arial, sans-serif;
  }
  .sheet {
    width: 1200px;
    height: 960px;
    display: flex;
    flex-direction: column;
    align-items: center;
    justify-content: center;
    gap: 60px;
  }
  .card {
    position: relative;
    width: 560px;
    height: 350px;
    box-shadow: 0 6px 18px rgba(0,0,0,0.18);
    overflow: hidden;
  }

  /* Front side */
  .card-front { background: var(--paper); }
  .brand {
    position: absolute;
    display: flex;
    align-items: center;
    gap: 10px;
    font-weight: 600;
    letter-spacing: 0.5px;
    white-space: nowrap;
  }
  .card-front .brand {
    top: 44px;
    right: 34px;
    font-size: 32px;
    color: var(--brand-deep);
  }
  .brand-dot {
    width: 16px;
    height: 16px;
    border-radius: 50%;
    background: currentColor;
    flex: none;
  }
  .holder-name {
    position: absolute;
    left: 34px;
    top: 182px;
    font-size: 30px;
    font-weight: 400;
    color: var(--ink);
    letter-spacing: 0.5px;
    text-transform: uppercase;
  }
  .name-rule {
    position: absolute;
    left: 34px;
    right: 34px;
    top: 232px;
    height: 1px;
    background: var(--rule);
  }
  .contact-list {
    position: absolute;
    left: 34px;
    right: 34px;
    top: 254px;
    display: flex;
    justify-content: space-between;
    list-style: none;
  }
  .contact-item {
    padding-left: 10px;
    border-left: 1px solid var(--rule);
  }
  .contact-item:first-child { padding-left: 0; border-left: none; }
  .contact-label {
    display: block;
    font-size: 13px;
    color: var(--ink-soft);
    line-height: 1.5;
    white-space: nowrap;
  }
  .contact-value {
    display: block;
    font-size: 14px;
    color: var(--ink);
    line-height: 1.5;
    white-space: nowrap;
  }
  .contact-value .accent { color: var(--brand-mid); }

  /* Back side */
  .card-back { background: var(--brand-mid); }
  .card-back svg { position: absolute; inset: 0; }
  .card-back .brand {
    top: 50%;
    left: 50%;
    transform: translate(-50%, -50%);
    font-size: 40px;
    color: var(--paper);
  }
</style>
</head>
<body>
<main class="sheet">
  <section class="card card-front" aria-label="Visittkort forside">
    <div class="brand"><span class="brand-dot"></span>Kjelvraket</div>
    <h1 class="holder-name">Leif Brattvoll</h1>
    <div class="name-rule"></div>
    <ul class="contact-list">
      <li class="contact-item">
        <span class="contact-label">Telephone:</span>
        <span class="contact-value">873 615 309</span>
      </li>
      <li class="contact-item">
        <span class="contact-label">Email:</span>
        <span class="contact-value">leif@fjordlast.no</span>
      </li>
      <li class="contact-item">
        <span class="contact-label">Post adress:</span>
        <span class="contact-value">8642 Raudvik</span>
      </li>
      <li class="contact-item">
        <span class="contact-label">Web adress:</span>
        <span class="contact-value">www.<span class="accent">fjordlast</span>.no</span>
      </li>
    </ul>
  </section>

  <section class="card card-back" aria-label="Visittkort bakside">
    <svg width="560" height="350" viewBox="0 0 560 350" aria-hidden="true">
      <defs>
        <linearGradient id="back-fill" x1="0" y1="0" x2="1" y2="1">
          <stop offset="0" stop-color="#1469c8"/>
          <stop offset="0.6" stop-color="#2a82dc"/>
          <stop offset="1" stop-color="#3d92e4"/>
        </linearGradient>
      </defs>
      <rect width="560" height="350" fill="url(#back-fill)"/>
      <path d="M0,170 C110,205 240,275 330,350 L0,350 Z" fill="#0b3a8e"/>
      <path d="M0,240 C80,265 170,305 230,350 L0,350 Z" fill="#0a3383" opacity="0.6"/>
      <path d="M395,0 C455,35 510,62 560,78 L560,0 Z" fill="#0b3a8e" opacity="0.85"/>
    </svg>
    <div class="brand"><span class="brand-dot"></span>Kjelvraket</div>
  </section>
</main>
</body>
</html>
```